Business Card Design - Photographer

I am a landscape photographer and I require a business card design. 

I require two designs:
1)  a double sided business card
 and
b)  a single sided business card 

The single sided design can either be the same as the double sided (with just one side having all the information)....or it can be an entire new design. Its up to you.

My corporate colours are (CMYK):

Blue   69, 32, 0, 0
Grey  72,  64,  47,  31
Green  32,  2,  91,  0
Yellow   0, 19, 92, 0
Orange  0, 39, 75, 0

Colour space in final file should be in CMYK.

The details that need to be included on the card:

- Use the provided Logo
- Name: Wiktor Baranowski
- Email:   sales@vistalumeworks.com.au
- Website:    vistalumeworks.com.au
- Twitter:    twitter.com/vistalumeworks
- Facebook:   facebook.com/vistalumeworks
- Mobile  0417 539 662

Please use the attached template to design the logo to the specified size, including the marked bleed lines. I have also attached my logo in PNG (transparent background) and ai format for you to use.

The final file should be:
- Photoshop version with layers so I can edit the name/text etc. All non vector files should be high resolution at 1039 x 697 pixels at 300 dpi.

I also require a file as:
- Vector based PDF

Anyway questions please contact me.

Thank you

Industry/Entity Type

Landscape

Logo styles of interest
Pictorial/Combination Logo
Abstract Logo
Wordmark Logo
Lettermark Logo
Requirements
Must have
• The details that need to be included on the card:

- Use the provided Logo
- Name: Wiktor Baranowski
- Email: sales@vistalumeworks.com.au
- Website: vistalumeworks.com.au
- Twitter: twitter.com/vistalumeworks
- Facebook: facebook.com/vistalumeworks
- Mobile 0417 539 662

```html
<!DOCTYPE html>
<html lang="en">
<head>
<meta charset="utf-8">
<title>Vistalume Works – Business Card</title>
<link href="https://fonts.googleapis.com/css2?family=Cinzel:wght@400;600&family=Open+Sans:wght@400&display=swap" rel="stylesheet">
<style>
  :root {
    --canvas-bg: #ececec;
    --card-bg: #ffffff;
    --ink-grey: #3f4458;
    --text-grey: #55585f;
    --brand-blue: #3b95d3;
    --brand-green: #b3cc3a;
    --brand-yellow: #ffcd27;
    --brand-orange: #fba050;
    --rule-grey: #b9bbc0;
  }
  * { box-sizing: border-box; margin: 0; padding: 0; }
  html, body { width: 1200px; height: 758px; overflow: hidden; }
  body {
    background: var(--canvas-bg);
    position: relative;
    font-family: "Open Sans", Arial, sans-serif;
    color: var(--text-grey);
  }
  .card {
    position: absolute;
    width: 520px;
    height: 297px;
    background: var(--card-bg);
    box-shadow: 0 6px 18px rgba(0,0,0,0.18);
  }
  .card--front { left: 50px; top: 230px; }
  .card--back  { left: 630px; top: 230px; }

  /* brand lockup */
  .brand {
    position: absolute;
    left: 0; right: 0;
    display: flex;
    align-items: center;
    justify-content: center;
    gap: 12px;
  }
  .brand__dot {
    border-radius: 50%;
    background: var(--ink-grey);
  }
  .brand__name {
    font-family: "Cinzel", "Times New Roman", serif;
    font-weight: 600;
    color: var(--ink-grey);
    letter-spacing: 0.04em;
  }
  .card--front .brand { top: 44px; }
  .card--front .brand__dot { width: 34px; height: 34px; }
  .card--front .brand__name { font-size: 24px; }

  .card--back .brand { top: 92px; }
  .card--back .brand__dot { width: 56px; height: 56px; }
  .card--back .brand__name { font-size: 28px; }

  /* website band on front */
  .web-band {
    position: absolute;
    left: 155px;
    top: 118px;
    width: 210px;
    height: 32px;
    background: var(--ink-grey);
    border-top: 2px solid var(--brand-orange);
    color: #ffffff;
    font-size: 12.5px;
    letter-spacing: 0.06em;
    display: flex;
    align-items: center;
    justify-content: center;
  }

  /* contact block */
  .contact {
    position: absolute;
    top: 182px;
    left: 0; right: 0;
    display: flex;
    justify-content: center;
    font-size: 12.5px;
    line-height: 20px;
  }
  .contact__address {
    text-align: right;
    padding-right: 12px;
    padding-top: 30px;
  }
  .contact__divider {
    width: 1px;
    background: var(--rule-grey);
    height: 84px;
  }
  .contact__list {
    list-style: none;
    padding-left: 10px;
  }
  .contact__item {
    display: flex;
    align-items: center;
    gap: 6px;
  }
  .contact__icon { width: 10px; height: 10px; flex: none; }

  .site-line {
    position: absolute;
    left: 0; right: 0;
    top: 200px;
    text-align: center;
    font-family: "Cinzel", "Times New Roman", serif;
    font-weight: 600;
    font-size: 16px;
    letter-spacing: 0.06em;
    color: var(--ink-grey);
  }
</style>
</head>
<body>

  <section class="card card--front" aria-label="Business card front">
    <div class="brand">
      <span class="brand__dot"></span>
      <span class="brand__name">Vistalume Works</span>
    </div>

    <div class="web-band">www.vistalumeworks.com.au</div>

    <div class="contact">
      <div class="contact__address">00, Complex name, state<br>city 0020</div>
      <div class="contact__divider"></div>
      <ul class="contact__list">
        <li class="contact__item">
          <svg class="contact__icon" viewBox="0 0 10 10"><rect x="2.5" y="0.5" width="5" height="9" rx="1" fill="var(--text-grey)"/><rect x="3.5" y="1.8" width="3" height="5" fill="#fff"/></svg>
          0417 539 662
        </li>
        <li class="contact__item">
          <svg class="contact__icon" viewBox="0 0 10 10"><rect x="0.5" y="2" width="9" height="6.5" fill="var(--text-grey)"/><path d="M0.8 2.3 L5 5.6 L9.2 2.3" stroke="#fff" stroke-width="0.8" fill="none"/></svg>
          sales@vistalumeworks.com.au
        </li>
        <li class="contact__item">
          <svg class="contact__icon" viewBox="0 0 10 10"><rect x="0.5" y="0.5" width="9" height="9" rx="1.5" fill="var(--brand-blue)"/></svg>
          vistalumeworks
        </li>
        <li class="contact__item">
          <svg class="contact__icon" viewBox="0 0 10 10"><rect x="0.5" y="0.5" width="9" height="9" rx="1.5" fill="#3b5998"/></svg>
          vistalumeworks
        </li>
      </ul>
    </div>
  </section>

  <section class="card card--back" aria-label="Business card back">
    <div class="brand">
      <span class="brand__dot"></span>
      <span class="brand__name">Vistalume Works</span>
    </div>
    <div class="site-line">www.vistalumeworks.com.au</div>
  </section>

</body>
</html>
```